Core Investment Strategy's Super Pie Chart

We need a one page visual explanation of an investment strategy we call "Keystone/Orbit". This strategy emphasizes a "core" portfolio that will seldom change and "perimeter" investments that will change. Our investment management firm caters to wealthy individuals. We want to project an image of strength and reliability. At the same time, we are willing to explore new concepts. I have uploaded a PDF of my graphically-challenged assistant's attempt at creating the one page visual.

```html
<!DOCTYPE html>
<html lang="en">
<head>
<meta charset="utf-8">
<title>Keystone/Orbit Portfolio</title>
<link href="https://fonts.googleapis.com/css2?family=Cinzel:wght@400&family=Cormorant+SC:wght@500&display=swap" rel="stylesheet">
<style>
  :root {
    --page: #ffffff;
    --panel-light: #f1f1f1;
    --panel-mid: #d9d9d9;
    --ink: #333333;
    --ink-soft: #4a4a4a;
    --slate: #55565a;
    --leaf: #8dc63f;
    --leaf-text: #5fb52a;
    --sky: #29abe2;
    --amber: #fbb03b;
    --orange: #f7931e;
    --tan: #c69c6d;
    --tan-text: #8c6239;
    --rule: #bdbdbd;
    --white: #ffffff;
  }
  * { box-sizing: border-box; margin: 0; padding: 0; }
  html, body { width: 1200px; height: 900px; overflow: hidden; background: var(--page); }
  .canvas { position: relative; width: 1200px; height: 900px; }
  .panel {
    position: absolute; left: 24px; top: 176px; width: 1152px; height: 648px;
    background: radial-gradient(ellipse at 60% 40%, var(--panel-light) 0%, #e6e6e6 55%, var(--panel-mid) 100%);
  }
  .chart { position: absolute; left: 0; top: 0; }
  .title {
    position: absolute; left: 534px; top: 282px;
    font-family: "Cinzel", serif; font-size: 38px; color: var(--ink); letter-spacing: 1px;
    white-space: nowrap;
  }
  .alloc { position: absolute; left: 605px; width: 500px; display: flex; align-items: baseline; white-space: nowrap;
    font-family: "Cinzel", serif; }
  .alloc .chev { width: 48px; height: 24px; flex: none; align-self: center; }
  .alloc .label { padding-left: 14px; }
  .alloc .leader { flex: 1; overflow: hidden; letter-spacing: 5px; padding: 0 2px; }
  .alloc .leader::after { content: "......................................................"; }
  .alloc .pct { flex: none; }
  .equity { color: var(--leaf-text); font-size: 28px; height: 36px; }
  .bond { color: var(--ink); font-size: 31px; height: 38px; }
  .bond .label { padding-left: 4px; }
  .divider { position: absolute; left: 557px; top: 522px; width: 533px; height: 2px; background: var(--rule); }
  .legend-item { position: absolute; display: flex; align-items: flex-start; gap: 8px;
    font-family: "Cormorant SC", serif; font-size: 14px; line-height: 1.05; }
  .legend-item .dot { width: 32px; height: 32px; border-radius: 50%; flex: none; }
  .legend-item .text { padding-top: 3px; }
  .others { left: 608px; top: 637px; color: var(--sky); font-size: 18px; }
  .others .text { padding-top: 6px; }
  .alternative { left: 608px; top: 672px; color: var(--orange); }
  .active { left: 757px; top: 637px; color: var(--tan-text); }
  .attractive { left: 757px; top: 676px; color: var(--ink); }
  .dot-sky { background: var(--sky); }
  .dot-orange { background: var(--orange); }
  .dot-tan { background: var(--tan); }
  .dot-white { background: var(--white); border: 1.5px solid var(--ink-soft); }
</style>
</head>
<body>
<div class="canvas">
  <div class="panel"></div>

  <svg class="chart" width="1200" height="900" viewBox="0 0 1200 900" aria-label="Allocation pie chart">
    <!-- header rule -->
    <line x1="100" y1="255" x2="945" y2="255" stroke="var(--ink)" stroke-width="3"/>
    <rect x="70" y="243" width="24" height="24" transform="rotate(45 82 255)" fill="var(--white)" stroke="var(--ink)" stroke-width="2.5"/>
    <circle cx="82" cy="255" r="6" fill="var(--sky)"/>

    <!-- outer ring -->
    <g fill="none" stroke-width="16">
      <path d="M115.1 509.8 A207 207 0 0 1 314.8 310.1" stroke="var(--sky)"/>
      <path d="M329.2 310.1 A207 207 0 0 1 528.9 509.8" stroke="var(--amber)"/>
      <path d="M528.9 524.2 A207 207 0 0 1 329.2 723.9" stroke="var(--tan)"/>
      <path d="M314.8 723.9 A207 207 0 0 1 115.1 524.2" stroke="var(--white)"/>
    </g>

    <!-- pie slices -->
    <g stroke="var(--white)" stroke-width="4" stroke-linejoin="round">
      <path d="M322 517 L322 327 A190 190 0 0 1 444.1 662.5 Z" fill="var(--leaf)"/>
      <path d="M322 517 L444.1 662.5 A190 190 0 0 1 393.2 693.2 Z" fill="var(--leaf)"/>
      <path d="M322 517 L393.2 693.2 A190 190 0 0 1 335.3 706.5 Z" fill="var(--leaf)"/>
      <path d="M322 517 L335.3 706.5 A190 190 0 0 1 221.3 678.1 Z" fill="var(--leaf)"/>
      <path d="M322 517 L221.3 678.1 A190 190 0 0 1 194.9 375.8 Z" fill="var(--slate)"/>
      <path d="M322 517 L194.9 375.8 A190 190 0 0 1 322 327 Z" fill="var(--slate)"/>
    </g>
    <circle cx="322" cy="517" r="30" fill="var(--white)"/>

    <!-- slice labels -->
    <g fill="var(--white)" font-family="Cinzel, serif" text-anchor="middle">
      <text x="402" y="470" font-size="46" transform="rotate(62 402 455)">30%</text>
      <text x="222" y="538" font-size="46" transform="rotate(-78 222 522)">20%</text>
      <text x="287" y="434" font-size="22">10%</text>
      <text x="307" y="640" font-size="22">10%</text>
      <text x="356" y="636" font-size="18" transform="rotate(75 356 630)">5%</text>
      <text x="393" y="620" font-size="18" transform="rotate(60 393 614)">5%</text>
    </g>
  </svg>

  <h1 class="title">Keystone Orbit Portfolio</h1>

  <div class="alloc equity" style="top:344px">
    <svg class="chev" viewBox="0 0 48 24"><path d="M0 0 H34 L48 12 L34 24 H0 L12 12 Z" fill="var(--leaf)"/></svg>
    <span class="label">Lg. Cap Equities</span><span class="leader"></span><span class="pct">30%</span>
  </div>
  <div class="alloc equity" style="top:383px">
    <svg class="chev" viewBox="0 0 48 24"><path d="M0 0 H34 L48 12 L34 24 H0 L12 12 Z" fill="var(--leaf)"/></svg>
    <span class="label">Mid Cap Equities</span><span class="leader"></span><span class="pct">05%</span>
  </div>
  <div class="alloc equity" style="top:422px">
    <svg class="chev" viewBox="0 0 48 24"><path d="M0 0 H34 L48 12 L34 24 H0 L12 12 Z" fill="var(--leaf)"/></svg>
    <span class="label">Sm. Cap Equities</span><span class="leader"></span><span class="pct">05%</span>
  </div>
  <div class="alloc equity" style="top:461px">
    <svg class="chev" viewBox="0 0 48 24"><path d="M0 0 H34 L48 12 L34 24 H0 L12 12 Z" fill="var(--leaf)"/></svg>
    <span class="label">Int'l/dev. Cap Equities</span><span class="leader"></span><span class="pct">10%</span>
  </div>

  <div class="divider"></div>

  <div class="alloc bond" style="top:546px">
    <svg class="chev" viewBox="0 0 48 24"><path d="M0 0 H34 L48 12 L34 24 H0 L12 12 Z" fill="var(--slate)"/></svg>
    <span class="label">Intermediate Bonds</span><span class="leader"></span><span class="pct">20%</span>
  </div>
  <div class="alloc bond" style="top:582px">
    <svg class="chev" viewBox="0 0 48 24"><path d="M0 0 H34 L48 12 L34 24 H0 L12 12 Z" fill="var(--slate)"/></svg>
    <span class="label">Short Term Bonds</span><span class="leader"></span><span class="pct">10%</span>
  </div>

  <div class="legend-item others"><span class="dot dot-sky"></span><span class="text">Others : 2%</span></div>
  <div class="legend-item alternative"><span class="dot dot-orange"></span><span class="text">Alternative<br>Assets : 7%</span></div>
  <div class="legend-item active"><span class="dot dot-tan"></span><span class="text">Actively Managed<br>Mutual Funds, 8%</span></div>
  <div class="legend-item attractive"><span class="dot dot-white"></span><span class="text">Attractive Core<br>Assets, 3%</span></div>
</div>
</body>
</html>
```